New design for www.TrimTable.com

On TrimTable you can find & book your hairdresser. TrimTable is the biggest platform in the Netherlands.

- The design should be a responcive design
- Should be able to go global, should fit in perfectly between all the big booking platforms like stayvo, ridlo etc,
- Should have te result of more bookings. :)
- We are ‘only’ asking a beautiful design, not a technical solution.
- We need a homepage (https://trimtable.com/), search resultpage ((https://trimtable.com/kapper/amsterdam/#), salonpage (https://trimtable.com/kapper/vorden/lumo-for-hair/), about us page (https://trimtable.com/aboutus/), for the hairdresser info page (https://trimtable.com/kapper/), login/register page (https://trimtable.com/account/signin/).

- On the page of the hairdresser there is a dynamic part. The part where you create your appointment. Please take a look at this part too after you choose your treatment (behandeling), employee (medewerker), Date (datum) and time (tijd). The part that you see after this, is the part where you fill in your data as a consumer.

I've added more logo's but mostly we use the green color.

A few of our competitors: www.plumsalo.com, www.korifex.com

Target Market(s)

All consumers

Industry/Entity Type

Hair And Beauty

Number of Pages Required

5+ page

Font styles to use
Sans Serif

Colors
abd036
c3c3c3
757575

Requirements
Must have
• Responsive
• We did an A/B test with the homepage. It turns out that option B works better then option A (take a look at the uploaded pictures). So what we need on the homepage: The USP's with the green checkboxes, The search button needs to by dynamic (changes for example from light green to dark green so you can see you can click it) The call to action sentence Zoek & Vind je kapsalon, the searchfield and searchbutton should be seperated.
Nice to have
• The style that we like is the flat design style. The website should be simple, clean and it should feel a bit like a luxury thing. Because an appointment with the hairdresser can be a real treat and luxury moment for yourself.
• The luxury feeling and flat design that is in the www.ridlo.com website is really nice for example. But then it has to be a bit more light and not so black and dark.

```html
<!DOCTYPE html>
<html lang="en">
<head>
<meta charset="utf-8">
<title>TrimTable – Find &amp; book your hairdresser</title>
<link rel="stylesheet" href="https://fonts.googleapis.com/css2?family=Open+Sans:wght@400;600;700&family=Lato:ital,wght@1,700&display=swap">
<style>
:root{
  --green:#abd036;
  --green-dark:#8fb324;
  --grey:#c3c3c3;
  --text:#757575;
  --ink:#333;
  --orange:#f0872b;
  --band:#ebebeb;
  --footer:#2f3033;
  --footer-deep:#242527;
  --white:#fff;
}
*{box-sizing:border-box;margin:0;padding:0}
html,body{width:1200px;height:2224px;overflow:hidden}
body{font-family:"Open Sans",Arial,sans-serif;color:var(--text);background:var(--white);font-size:14px}
.page{position:relative;width:1200px;height:2224px}

/* header */
.topbar{height:70px;display:flex;align-items:center;padding:0 70px;position:relative}
.brand{display:flex;align-items:center;gap:8px;font-weight:700;font-size:26px;color:var(--green)}
.brand-dot{width:30px;height:30px;border-radius:50%;background:var(--green)}
.contacts{display:flex;gap:36px;margin-left:auto;margin-top:14px}
.contact{display:flex;gap:8px;align-items:center}
.contact svg{width:22px;height:22px}
.contact small{display:block;font-size:10px;color:var(--grey)}
.contact b{font-size:12px;color:var(--ink);font-weight:600}
.account{position:absolute;right:70px;top:0;background:var(--footer);color:var(--white);font-size:10px;padding:3px 10px;display:flex;gap:14px}
.mainnav{height:32px;background:var(--green);display:flex;align-items:center;padding:0 0 0 270px}
.mainnav a{color:var(--white);text-decoration:none;font-size:13px;font-weight:600;padding:0 22px}
.mainnav .cta{background:var(--footer);height:32px;line-height:32px;margin-left:10px;font-size:12px;text-transform:uppercase}

/* hero */
.hero{height:498px;position:relative;background:linear-gradient(180deg,#4c4f53 0%,#2f3236 60%,#3d3f42 100%);text-align:center;color:var(--white)}
.hero-photo{position:absolute;inset:0;background:linear-gradient(90deg,rgba(0,0,0,.35),rgba(90,90,90,.15),rgba(0,0,0,.35))}
.hero h1{position:relative;padding-top:140px;font-family:"Lato",Arial,sans-serif;font-style:italic;font-weight:700;font-size:40px;line-height:50px;text-shadow:0 2px 4px rgba(0,0,0,.5)}
.search{position:relative;margin:50px auto 0;width:540px;display:flex;gap:10px}
.search-field{flex:1;height:46px;background:var(--white);border-radius:3px;display:flex;align-items:center;padding-left:14px;color:var(--grey);font-size:13px;gap:8px}
.search-btn{width:90px;height:46px;background:var(--white);border-radius:3px;color:var(--ink);font-weight:600;line-height:46px}
.search-options{position:relative;width:540px;margin:14px auto 0;display:flex;gap:10px}
.search-options span{flex:1;height:40px;line-height:40px;text-align:left;padding-left:14px;font-size:13px;background:rgba(0,0,0,.35);border:1px solid rgba(255,255,255,.3)}
.search-options span:last-child{flex:0 0 200px}

/* about */
.about{height:360px;position:relative;padding:60px 0 0 88px}
.title{font-size:34px;font-weight:700;color:var(--green);text-align:center}
.title em{font-style:normal;color:var(--orange)}
.title-rule{display:block;width:70px;height:3px;background:var(--green);margin:6px auto 0}
.about .title{position:absolute;left:0;right:0;top:50px}
.about-copy{width:580px;margin-top:70px;font-size:12px;line-height:20px}
.usps{list-style:none;margin-top:10px}
.usps li{display:flex;align-items:center;gap:8px;font-size:12px;line-height:22px;color:var(--ink)}
.usps svg{width:14px;height:14px}
.btn{display:inline-block;background:var(--green);color:var(--white);font-size:11px;font-weight:600;padding:7px 16px;border-radius:2px;text-decoration:none}
.about .btn{margin-top:12px}
.portrait-small{position:absolute;left:720px;top:130px;width:130px;height:130px;border-radius:50%;background:linear-gradient(135deg,#5b3b2c,#c7a38a)}
.portrait-large{position:absolute;left:845px;top:95px;width:270px;height:270px;border-radius:50%;border:6px solid var(--orange);background:linear-gradient(135deg,#f4dccb,#e9b99c)}

/* app band */
.app{height:360px;background:var(--band);position:relative}
.phones{position:absolute;left:185px;top:45px;width:340px;height:270px;background:linear-gradient(135deg,#f7f7f7,#cfd3d6);border-radius:18px}
.app-copy{position:absolute;left:600px;top:110px;width:480px}
.app-copy h2{font-size:22px;font-weight:700;color:var(--ink);line-height:30px;text-transform:uppercase}
.app-copy p{font-size:15px;margin-top:12px;line-height:22px}
.app-copy .btn{margin-top:18px;font-size:10px;text-transform:uppercase}

/* how */
.how{height:580px;position:relative;padding-top:70px}
.steps{display:flex;justify-content:center;gap:40px;margin-top:50px}
.step{width:260px;text-align:center}
.step-icon{width:200px;height:200px;border-radius:50%;background:var(--green);margin:0 auto;display:flex;align-items:center;justify-content:center;border:8px solid #d9e9a5}
.step-icon svg{width:90px;height:90px}
.step-card{background:var(--white);box-shadow:0 2px 8px rgba(0,0,0,.12);margin-top:-20px;padding:40px 20px 24px}
.step-card h3{font-size:15px;color:var(--ink);font-weight:600;line-height:20px}
.step-card p{font-size:11px;margin-top:10px;line-height:17px}

/* footer */
.footer{height:296px;background:var(--footer);color:#cfcfcf;position:relative;padding:30px 0 0 100px;display:flex}
.footer h4{color:var(--white);font-size:14px;font-weight:600;margin-bottom:16px}
.quick{width:210px}
.quick li{list-style:none;font-size:11px;line-height:22px}
.quick li::before{content:"› ";color:var(--green)}
.appoint{width:290px}
.field{height:28px;background:var(--white);border-radius:2px;margin-bottom:8px}
.field.tall{height:56px}
.row{display:flex;gap:8px}
.row .field{flex:1}
.appoint .btn{font-size:10px;padding:5px 12px}
.contact-detail{width:190px;margin-left:68px}
.contact-detail li{list-style:none;display:flex;gap:8px;font-size:11px;line-height:16px;margin-bottom:12px}
.contact-detail svg{flex:0 0 14px;height:14px}
.map{position:absolute;left:880px;top:60px;width:240px;height:170px;background:linear-gradient(135deg,#e7e3da,#cfd8c6)}
.bottom{height:28px;background:var(--footer-deep);color:#9a9a9a;font-size:10px;display:flex;align-items:center;justify-content:space-between;padding:0 80px}
</style>
</head>
<body>
<div class="page">

<header class="topbar">
  <div class="brand"><span class="brand-dot"></span>TrimTable</div>
  <div class="contacts">
    <div class="contact">
      <svg viewBox="0 0 24 24"><circle cx="12" cy="12" r="11" fill="var(--green)"/><path d="M8 6l3 3-2 2c1 2 2 3 4 4l2-2 3 3-2 2c-5 0-10-5-10-10z" fill="#fff"/></svg>
      <div><small>Phone Number</small><b>123-456-7890</b></div>
    </div>
    <div class="contact">
      <svg viewBox="0 0 24 24"><circle cx="12" cy="12" r="11" fill="var(--green)"/><circle cx="12" cy="12" r="6" fill="none" stroke="#fff" stroke-width="2"/><path d="M12 9v3l2 2" stroke="#fff" stroke-width="2" fill="none"/></svg>
      <div><small>Working Hours</small><b>07:00am-05:00pm</b></div>
    </div>
    <div class="contact">
      <svg viewBox="0 0 24 24"><circle cx="12" cy="12" r="11" fill="var(--green)"/><rect x="6" y="8" width="12" height="8" fill="none" stroke="#fff" stroke-width="1.6"/><path d="M6 8l6 5 6-5" fill="none" stroke="#fff" stroke-width="1.6"/></svg>
      <div><small>Send Message</small><b>contact@trimtable.com</b></div>
    </div>
  </div>
  <div class="account"><span>LOGIN ▾</span><span>REGISTER ▾</span></div>
</header>

<nav class="mainnav">
  <a href="#">Home</a><a href="#">About Us</a><a href="#">Hairdresser</a><a href="#">Salon</a><a href="#">Contact Us</a>
  <a href="#" class="cta">Make an Appointment</a>
</nav>

<section class="hero">
  <div class="hero-photo" role="img" aria-label="Photo of a modern hair salon interior with styling chairs and mirrors"></div>
  <h1>The Greatest Hairdressers Booking<br>Site In The Netherlands With<br>542 Hairdressers</h1>
  <div class="search">
    <div class="search-field">
      <svg width="14" height="14" viewBox="0 0 24 24"><circle cx="10" cy="10" r="7" fill="none" stroke="#999" stroke-width="2.5"/><path d="M15 15l6 6" stroke="#999" stroke-width="2.5"/></svg>
      Search by city or zip code
    </div>
    <div class="search-btn">Search</div>
  </div>
  <div class="search-options">
    <span>🔍 Search Salon Name</span>
    <span>Any Distance ▾</span>
  </div>
</section>

<section class="about">
  <h2 class="title">About <em>Us</em><span class="title-rule"></span></h2>
  <p class="about-copy">TrimTable helps you find the right hairdresser near you and book an appointment in a few clicks. Compare salons, read honest reviews from other guests and choose the time that suits you best. From a quick trim to a complete new look, every visit becomes a small moment of luxury just for you, without phone calls or waiting.</p>
  <ul class="usps">
    <li><svg viewBox="0 0 16 16"><rect width="16" height="16" rx="2" fill="var(--orange)"/><path d="M4 8l3 3 5-6" stroke="#fff" stroke-width="2" fill="none"/></svg>Book online day and night</li>
    <li><svg viewBox="0 0 16 16"><rect width="16" height="16" rx="2" fill="var(--orange)"/><path d="M4 8l3 3 5-6" stroke="#fff" stroke-width="2" fill="none"/></svg>Real reviews from guests</li>
    <li><svg viewBox="0 0 16 16"><rect width="16" height="16" rx="2" fill="var(--orange)"/><path d="M4 8l3 3 5-6" stroke="#fff" stroke-width="2" fill="none"/></svg>No extra booking costs</li>
    <li><svg viewBox="0 0 16 16"><rect width="16" height="16" rx="2" fill="var(--orange)"/><path d="M4 8l3 3 5-6" stroke="#fff" stroke-width="2" fill="none"/></svg>Instant confirmation by email</li>
  </ul>
  <a href="#" class="btn">Read More</a>
  <div class="portrait-small" role="img" aria-label="Photo of a client with styled hair"></div>
  <div class="portrait-large" role="img" aria-label="Photo of a smiling woman with freshly styled hair"></div>
</section>

<section class="app">
  <div class="phones" role="img" aria-label="Two smartphones showing the TrimTable mobile app screens"></div>
  <div class="app-copy">
    <h2>All the hairdressers of Netherlands in your pocket?</h2>
    <p>Download the mobile app and always find a place to make it a good hairday :)</p>
    <a href="#" class="btn">Download the app</a>
  </div>
</section>

<section class="how">
  <h2 class="title">How Does It <em>Work?</em><span class="title-rule"></span></h2>
  <div class="steps">
    <div class="step">
      <div class="step-icon">
        <svg viewBox="0 0 64 64" fill="none" stroke="#fff" stroke-width="4"><circle cx="16" cy="48" r="8"/><circle cx="48" cy="48" r="8"/><path d="M22 42L50 8M42 42L14 8"/></svg>
      </div>
      <div class="step-card"><h3>Search &amp; Find<br>hairdresser</h3><p>Search by city or salon name and compare prices, treatments and reviews easily.</p></div>
    </div>
    <div class="step">
      <div class="step-icon">
        <svg viewBox="0 0 64 64" fill="none" stroke="#fff" stroke-width="4"><rect x="8" y="12" width="48" height="44" rx="3"/><path d="M8 24h48M20 6v12M44 6v12M22 40l7 7 14-14"/></svg>
      </div>
      <div class="step-card"><h3>Book your appointment<br>online with 100% certainty</h3><p>Pick a treatment, stylist, date and time and get your confirmation right away.</p></div>
    </div>
    <div class="step">
      <div class="step-icon">
        <svg viewBox="0 0 64 64" fill="#fff"><path d="M32 4l7 19 20 1-16 12 6 20-17-12-17 12 6-20L5 24l20-1z"/></svg>
      </div>
      <div class="step-card"><h3>Enjoy your new<br>hairstyle</h3><p>Relax in the chair, enjoy the treatment and leave with a look you love.</p></div>
    </div>
  </div>
</section>

<footer class="footer">
  <div class="quick">
    <h4>Quick Links</h4>
    <ul><li>Home</li><li>About Us</li><li>Hairdresser</li><li>Salon</li><li>Contact Us</li></ul>
  </div>
  <div class="appoint">
    <h4>Make an Appointment</h4>
    <div class="row"><div class="field"></div><div class="field"></div></div>
    <div class="field"></div>
    <div class="row"><div class="field"></div><div class="field"></div></div>
    <div class="field tall"></div>
    <a href="#" class="btn">Submit</a>
  </div>
  <div class="contact-detail">
    <h4>Contact Detail</h4>
    <ul>
      <li><svg viewBox="0 0 24 24"><path d="M12 2a7 7 0 0 0-7 7c0 5 7 13 7 13s7-8 7-13a7 7 0 0 0-7-7z" fill="var(--green)"/><circle cx="12" cy="9" r="2.5" fill="var(--footer)"/></svg>12 Keizerslaan, 1017 AB Amsterdam, Netherlands</li>
      <li><svg viewBox="0 0 24 24"><path d="M6 3l4 4-2 3c1 3 3 5 6 6l3-2 4 4-3 3C10 21 3 14 3 6z" fill="var(--green)"/></svg>(123) 456-7890</li>
      <li><svg viewBox="0 0 24 24"><path d="M6 3l4 4-2 3c1 3 3 5 6 6l3-2 4 4-3 3C10 21 3 14 3 6z" fill="var(--green)"/></svg>(123) 456-7891</li>
      <li><svg viewBox="0 0 24 24"><rect x="3" y="6" width="18" height="12" fill="var(--green)"/><path d="M3 6l9 7 9-7" stroke="var(--footer)" stroke-width="1.5" fill="none"/></svg>contact@trimtable.com</li>
    </ul>
  </div>
  <div class="map" role="img" aria-label="Map showing the TrimTable office location"></div>
</footer>
<div class="bottom"><span>Copyright © 2015 TrimTable</span><span>Privacy Policy | Terms &amp; Conditions</span></div>

</div>
</body>
</html>
```